Redo a PPT pres. - Real Estate in Brazil - Socially equitable investments in Social Housing

We need to redo the presentation attached. It is an institutional presentation to attract local and foreign investors to invest in Brazilian Social Housing Projects structured by our company "TLR".
A middle class of 100 million, a housing deficit of 9M, a strong political will & positive income generation trends constitute grounds for a significant demand in social housing.
This make a perfect scheme for investors to invest in Brazilian Social Housing.
"TLR", is a consulting "boutique" focused in Brazilian real estate, specialized in structuring, analyzing and originating Brazilian social housing projects.
TLR is part of the group TLB. TLB is structured to create value through each step of the residential real estate business - structuring, financing, sales, marketing and technology.
We would like to see designs that use mainly the color blue. The final design should communicate financial safety and professionalism. In order to reach our needs, the designer will need to have basic understanding of finance and investment in order to highlight the most important information.
The idea is to receive back the PPT with each page redesigned and an homogeneous identity.
To all designers,
Target Market(s)
Institutional Investors and wealthy individuals
Industry/Entity Type
Residential
Look and feel

```html
<!DOCTYPE html>
<html lang="en">
<head>
<meta charset="utf-8">
<title>Social Housing in Brazil – TLR</title>
<link rel="stylesheet" href="https://fonts.googleapis.com/css2?family=Open+Sans:wght@400;600;700&display=swap">
<style>
  :root {
    --navy: #0d1a4a;
    --navy-deep: #070f33;
    --navy-mid: #1b2f7a;
    --blue: #2f6fd1;
    --blue-light: #4f8fe0;
    --sky: #8ab4ec;
    --grey: #8a8a8a;
    --grey-text: #6b6b6b;
    --white: #ffffff;
    --page: #ffffff;
  }
  * { box-sizing: border-box; margin: 0; padding: 0; }
  html, body { width: 1200px; height: 329px; overflow: hidden; background: var(--page); }
  body { position: relative; font-family: "Open Sans", Arial, sans-serif; }

  .slide {
    position: absolute; top: 47px; width: 329px; height: 250px;
    background: var(--white); overflow: hidden;
    box-shadow: 2px 2px 6px rgba(0,0,0,.35);
  }
  .slide--cover { left: 33px; }
  .slide--invest { left: 434px; }
  .slide--timing { left: 824px; }

  .brand { position: absolute; color: var(--navy); font-weight: 400; letter-spacing: .5px; }
  .slide--cover .brand { left: 11px; top: 24px; font-size: 12px; }
  .slide-footer .brand { left: 18px; bottom: 6px; font-size: 8px; }

  .skyline {
    position: absolute; left: 0; top: 42px; width: 100%; height: 116px;
    background: linear-gradient(180deg, #ffffff 0%, #8fa8e6 35%, #3d55b4 70%, #15246a 100%);
  }
  .cover-band {
    position: absolute; left: 0; top: 158px; width: 100%; height: 92px;
    background: linear-gradient(180deg, var(--navy-mid) 0%, var(--navy-deep) 100%);
  }
  .cover-title { position: absolute; left: 27px; top: 20px; color: var(--white); font-size: 13px; font-weight: 600; }
  .cover-subtitle { position: absolute; left: 27px; top: 57px; color: var(--sky); font-size: 9.5px; letter-spacing: .2px; }

  .slide-header {
    height: 42px; padding: 13px 0 0 14px;
    background: linear-gradient(180deg, var(--navy-deep) 0%, var(--navy-mid) 100%);
    color: var(--white); font-size: 13px; font-weight: 400;
  }
  .slide-lead { margin: 4px 0 0 14px; color: var(--blue); font-size: 10px; font-weight: 600; line-height: 14px; }

  .cycle { position: absolute; left: 0; top: 0; }
  .cycle text { font-family: "Open Sans", Arial, sans-serif; font-size: 4.6px; fill: var(--white); text-anchor: middle; font-weight: 600; }

  .slide-footer .page-no { position: absolute; right: 60px; bottom: 7px; font-size: 5px; color: var(--grey); }
  .footer-art {
    position: absolute; right: 6px; bottom: 0; width: 50px; height: 12px;
    background: linear-gradient(180deg, #2a3a80, var(--navy-deep));
  }

  .agenda { list-style: none; margin: 5px 0 0 16px; }
  .agenda li { font-size: 9.6px; line-height: 22.5px; color: var(--grey-text); white-space: nowrap; }
  .agenda .num { color: var(--blue-light); display: inline-block; width: 14px; }
  .agenda .topic { color: var(--blue-light); }
  .agenda .wrap { display: block; padding-left: 14px; line-height: 12px; margin-top: -4px; margin-bottom: 6px; }
</style>
</head>
<body>

<section class="slide slide--cover">
  <div class="brand">TLR</div>
  <div class="skyline" role="img" aria-label="Illustrated night city skyline in blue tones"></div>
  <div class="cover-band">
    <h1 class="cover-title">SOCIAL HOUSING IN BRAZIL</h1>
    <p class="cover-subtitle">HIGH YIELD RETURN FOR A QUASI SOVEREIGN RISK</p>
  </div>
</section>

<section class="slide slide--invest">
  <h2 class="slide-header">HOW TO INVEST IN SOCIAL HOUSING IN BRAZIL?</h2>
  <p class="slide-lead">A socially conscious &amp; lucrative investment</p>
  <svg class="cycle" width="329" height="250" viewBox="0 0 329 250">
    <circle cx="157" cy="150" r="66" fill="none" stroke="#3a4f9a" stroke-width="1"/>
    <rect x="121" y="66" width="68" height="24" fill="#1b2f7a"/>
    <text x="155" y="76">Building housing units for</text><text x="155" y="82">low to middle-class buyers</text>
    <rect x="180" y="96" width="68" height="26" fill="#1b2f7a"/>
    <text x="214" y="108">Investing in individual</text><text x="214" y="114">projects</text>
    <rect x="192" y="136" width="70" height="28" fill="#1b2f7a"/>
    <text x="227" y="146">Management</text><text x="227" y="152">Specialised International &amp;</text><text x="227" y="158">local team</text>
    <rect x="184" y="179" width="70" height="26" fill="#24398a"/>
    <text x="219" y="190">Co-investing with local /</text><text x="219" y="196">mid-size developers</text>
    <rect x="121" y="208" width="70" height="26" fill="#2c48a4"/>
    <text x="156" y="219">Co-financed by</text><text x="156" y="225">government</text>
    <rect x="62" y="179" width="70" height="26" fill="#1f3a9a"/>
    <text x="97" y="190">Equity participation of</text><text x="97" y="196">R$2-10 millions</text>
    <rect x="52" y="138" width="68" height="26" fill="#4f8fe0"/>
    <text x="86" y="149">Time Horizon</text><text x="86" y="155">3-4 years</text>
    <rect x="62" y="99" width="68" height="26" fill="#8a8a8a"/>
    <text x="96" y="110">Target IRR</text><text x="96" y="116">25-30%</text>
  </svg>
  <footer class="slide-footer">
    <div class="brand">TLR</div>
    <span class="page-no">2</span>
    <div class="footer-art" role="img" aria-label="Small city skyline silhouette"></div>
  </footer>
</section>

<section class="slide slide--timing">
  <h2 class="slide-header">THE TIME IS NOW!</h2>
  <ol class="agenda">
    <li><span class="num">1.</span><span class="topic">Macro-environment &amp; Mortgage market:</span> Green Light</li>
    <li><span class="num">2.</span><span class="topic">A sophisticated &amp; successful program:</span> Catalyst</li>
    <li><span class="num">3.</span><span class="topic">Investment Structure of a typical project:</span> Leverage &amp;<span class="wrap">Limited Risks</span></li>
    <li><span class="num">4.</span><span class="topic">Small &amp; mid size developers:</span> A partner by choice</li>
    <li><span class="num">5.</span><span class="topic">TLR:</span> Value added &amp; Risk mitigation</li>
    <li><span class="num">6.</span><span class="topic">TLB:</span> TLR, part of an integrated family of companies</li>
    <li><span class="num">7.</span><span class="topic">Appendix:</span> Next step…TLR Fund (2013)</li>
  </ol>
  <footer class="slide-footer">
    <div class="brand">TLR</div>
    <span class="page-no">3</span>
    <div class="footer-art" role="img" aria-label="Small city skyline silhouette"></div>
  </footer>
</section>

</body>
</html>
```